Business Card Design

Please see my website www.qvleading.com.au to for further information on my services and styling of my site
Updates

Project Deadline Extended
Reason: Deadline is extended to permit alterations to current designs or for any new submissions. Cheers

Industry/Entity Type

Business

Contact Information for Business Card

Marcus Belton
Empowerment Coach

'Live your passion'

marcus@qvleading.com.au
0437158206
qvleading.com.au

```html
<!DOCTYPE html>
<html lang="en">
<head>
<meta charset="utf-8">
<title>Quest &amp; Vantage Leading — Business Card</title>
<link rel="stylesheet" href="https://fonts.googleapis.com/css2?family=Josefin+Sans:wght@300;400&family=Roboto+Condensed:wght@700&family=Kaushan+Script&display=swap">
<style>
  :root {
    --backdrop: #d9d9d9;
    --card: #2a2728;
    --card-edge: #3a3637;
    --lime: #a9c23a;
    --white: #f4f4f4;
    --grey: #9a9a9a;
  }
  * { margin: 0; padding: 0; box-sizing: border-box; }
  html, body {
    width: 1200px; height: 900px; overflow: hidden;
    background: var(--backdrop);
  }
  .canvas {
    position: relative; width: 1200px; height: 900px;
    display: flex; flex-direction: column; align-items: center; justify-content: center; gap: 50px;
  }
  .card {
    position: relative; width: 700px; height: 400px;
    border-radius: 26px;
    background: linear-gradient(135deg, var(--card-edge) 0%, var(--card) 55%, #1f1d1e 100%);
    box-shadow: 0 12px 30px rgba(0,0,0,0.25);
    overflow: hidden;
  }

  /* Front */
  .front-brand {
    position: absolute; left: 80px; top: 50%; transform: translateY(-50%);
    display: flex; align-items: center; gap: 34px;
  }
  .brand-square {
    width: 150px; height: 130px; background: var(--white);
  }
  .front-name {
    font-family: "Roboto Condensed", sans-serif; font-weight: 700;
    font-size: 30px; color: var(--white); letter-spacing: 0.5px;
  }

  /* Back */
  .tagline {
    position: absolute; left: 200px; top: 58px;
    font-family: "Kaushan Script", cursive; font-size: 46px;
    color: var(--lime); transform: rotate(9deg); transform-origin: left center;
    white-space: nowrap;
  }
  .back-brand {
    position: absolute; right: 36px; top: 44px;
  }
  .back-brand .mark {
    display: flex; align-items: center; gap: 8px;
    font-family: "Roboto Condensed", sans-serif; font-weight: 700;
    font-size: 16px; color: var(--white); line-height: 1;
  }
  .back-brand .mark-square { width: 22px; height: 22px; background: var(--white); flex: none; }
  .back-brand .rule { height: 2px; background: var(--white); margin-top: 8px; }
  .person {
    position: absolute; left: 46px; top: 162px;
  }
  .person-name {
    font-family: "Josefin Sans", sans-serif; font-weight: 300;
    font-size: 50px; color: var(--lime); line-height: 1;
  }
  .person-role {
    font-family: "Josefin Sans", sans-serif; font-weight: 300;
    font-size: 14px; letter-spacing: 3px; color: var(--lime); margin-top: 6px;
  }
  .divider {
    position: absolute; left: 372px; top: 250px; width: 2px; height: 100px;
    background: linear-gradient(to bottom, transparent, var(--lime), transparent);
  }
  .contact {
    position: absolute; left: 400px; top: 268px;
    font-family: "Josefin Sans", sans-serif; font-size: 17px; line-height: 1.35;
    list-style: none;
  }
  .contact .label { color: var(--lime); font-weight: 400; }
  .contact .value { color: var(--grey); font-weight: 300; letter-spacing: 1px; }
</style>
</head>
<body>
<main class="canvas">
  <section class="card card-front" aria-label="Card front">
    <div class="front-brand">
      <div class="brand-square"></div>
      <div class="front-name">Quest &amp; Vantage Leading</div>
    </div>
  </section>

  <section class="card card-back" aria-label="Card back">
    <p class="tagline">Live your passion</p>
    <div class="back-brand">
      <div class="mark"><span class="mark-square"></span><span>Quest &amp; Vantage Leading</span></div>
      <div class="rule"></div>
    </div>
    <div class="person">
      <h1 class="person-name">Marcus Belton</h1>
      <p class="person-role">EMPOWERMENT COACH</p>
    </div>
    <div class="divider"></div>
    <ul class="contact">
      <li><span class="label">phone:</span> <span class="value">0437158206</span></li>
      <li><span class="label">email:</span> <span class="value">marcus@qvleading.com.au</span></li>
      <li><span class="label">web:</span> <span class="value">qvleading.com.au</span></li>
    </ul>
  </section>
</main>
</body>
</html>
```